UI/ UX Design for ERP Software

We need a new UX/UI interface for a ERP software for property managers. Our CMMS / ERP solution is made based on responsive design technologies and is coded in PHP.
The overall UX to be similar to Tev Ulna - easy navigation, intuitive menus.

Industry/Entity Type

Property Management

Number of Pages Required

5+ page

Requirements
Must have
• Round dock buttons
Consistent icons across the application
Enough Spacing between buttons/icons/ menu
Consistent Font
Nice to have
• We would like the UX to allow the users to use the application without /minimum training.
Should not have
• we don't want anything that is classic with respect to UX

```html
<!DOCTYPE html>
<html lang="en">
<head>
<meta charset="utf-8">
<title>Keyhold – Active Dashboard</title>
<link href="https://fonts.googleapis.com/css2?family=Nunito+Sans:wght@400;600;700&display=swap" rel="stylesheet">
<style>
:root{
  --bg:#506279;
  --pill:#2e3b4d;
  --white:#ffffff;
  --active:#14b4ff;
  --blue:#0a7cff;
  --tab:#00baff;
  --heading:#4a5a70;
  --axis-text:#4d5566;
  --track:#efefef;
  --legend-blue:#0a7cff;
  --legend-green:#8ee87a;
  --legend-orange:#f5a053;
  --legend-dark:#3f3f48;
  --legend-violet:#8087e6;
  --legend-pink:#f05a7e;
  --legend-yellow:#e5d64d;
}
*{box-sizing:border-box;margin:0;padding:0}
html,body{width:1200px;height:951px;overflow:hidden}
body{background:var(--bg);font-family:"Nunito Sans",sans-serif;color:var(--white);position:relative}
.brand{position:absolute;left:47px;top:24px;display:flex;align-items:center;gap:7px;font-size:19px;font-weight:700}
.brand-mark{width:12px;height:12px;background:var(--white);border-radius:50%}
.nav{position:absolute;left:0;top:80px;width:247px;list-style:none}
.nav li{position:relative;height:36.15px;display:flex;align-items:center;padding-left:60px;font-size:12px;letter-spacing:.2px}
.nav li svg.ic{position:absolute;left:38px;width:16px;height:16px;fill:none;stroke:currentColor;stroke-width:1.2}
.nav li.current{color:var(--active)}
.nav .caret{position:absolute;left:209px;width:0;height:0;border-left:5px solid var(--active);border-top:4px solid transparent;border-bottom:4px solid transparent}
.nav .more{position:absolute;left:209px;width:10px;height:10px;border-radius:50%;background:#c9d0da}
.nav .more::before,.nav .more::after{content:"";position:absolute;background:var(--bg);left:2px;top:4.4px;width:6px;height:1.2px}
.nav .more::after{transform:rotate(90deg)}
.topbar-home{position:absolute;left:240px;top:23px;width:30px;height:30px;border-radius:50%;background:#5f7089;display:flex;align-items:center;justify-content:center}
.topbar-title{position:absolute;left:277px;top:30px;font-size:12px;font-weight:600}
.stat{position:absolute;top:19.5px;height:38px;border-radius:19px;background:var(--pill);display:flex;align-items:center;padding-left:36px;font-size:10.5px;line-height:13px;color:#dfe5ee}
.stat svg{position:absolute;left:10px;top:10px;width:18px;height:18px;fill:none;stroke:#c8d0db;stroke-width:1}
.card{position:absolute;left:247px;top:98.5px;width:953px;height:618px;background:var(--white);border-radius:39px}
.tabs{position:absolute;left:269px;top:0;display:flex;gap:1.7px}
.tab{width:107px;height:40.5px;background:var(--tab);display:flex;align-items:center;justify-content:center;gap:3px;font-size:9px;font-weight:700;letter-spacing:.1px}
.tab.selected{background:linear-gradient(180deg,#0b9cff,#0a72ff)}
.tab i{width:7px;height:7px;border:1.2px solid var(--white);border-radius:50%}
.range{position:absolute;left:53px;top:52px;font-size:24.5px;font-weight:600;color:var(--heading);letter-spacing:1.4px;word-spacing:4px}
.y-title{position:absolute;left:17px;top:391px;transform:rotate(-90deg);transform-origin:left top;font-size:9px;color:#00aef0;letter-spacing:.5px;font-weight:600}
.chart{position:absolute;left:0;top:0}
.legend{position:absolute;left:64px;top:526px;width:880px;height:34px}
.legend-item{position:absolute;top:0;display:flex;align-items:center;gap:6px;font-size:9.3px;line-height:11.3px;color:var(--axis-text);font-weight:600}
.legend-item span.dot{width:28px;height:28px;border-radius:50%;flex:none}
</style>
</head>
<body>
<svg width="0" height="0" style="position:absolute">
  <defs>
    <symbol id="i-home" viewBox="0 0 16 16"><path d="M2 7.5 8 2l6 5.5M3.5 6.5V14h9V6.5M6.5 14v-4h3v4"/></symbol>
    <symbol id="i-user" viewBox="0 0 16 16"><circle cx="8" cy="8" r="6.5"/><circle cx="8" cy="6.5" r="2.3"/><path d="M4 12.8c1-2 2.3-2.8 4-2.8s3 .8 4 2.8"/></symbol>
    <symbol id="i-gear" viewBox="0 0 16 16"><circle cx="8" cy="8" r="2.4"/><path d="M8 1.5v2M8 12.5v2M1.5 8h2M12.5 8h2M3.4 3.4l1.4 1.4M11.2 11.2l1.4 1.4M3.4 12.6l1.4-1.4M11.2 4.8l1.4-1.4"/><circle cx="8" cy="8" r="4.6"/></symbol>
    <symbol id="i-doc" viewBox="0 0 16 16"><path d="M3.5 1.5h6l3 3v10h-9z"/><path d="M9.5 1.5v3h3M6 12l2-4 2 4"/></symbol>
    <symbol id="i-code" viewBox="0 0 16 16"><rect x="1.5" y="2.5" width="13" height="11"/><path d="M1.5 5h13M6 8 4.5 9.5 6 11M10 8l1.5 1.5L10 11M8.7 7.5l-1.4 4"/></symbol>
    <symbol id="i-search" viewBox="0 0 16 16"><circle cx="7" cy="7" r="4.5"/><path d="m10.3 10.3 3.7 3.7"/></symbol>
    <symbol id="i-chart" viewBox="0 0 16 16"><path d="M2 14.5h12.5M3 14V11h2v3M7 14V8h2v6M11 14V5h2v9M3 8l4-3 3 1 4-4"/></symbol>
    <symbol id="i-warn" viewBox="0 0 16 16"><path d="M8 1.8 14.6 14H1.4z"/><path d="M8 6.5v4M8 12v.6"/></symbol>
    <symbol id="i-list" viewBox="0 0 16 16"><rect x="2" y="2" width="12" height="12" rx="1"/><path d="M2 5.5h12M2 8.5h12M2 11.5h12"/></symbol>
    <symbol id="i-money" viewBox="0 0 16 16"><rect x="1.5" y="5" width="13" height="8" rx="1"/><circle cx="8" cy="9" r="2"/><path d="M3 5l8-3 1.5 3"/></symbol>
    <symbol id="i-chat" viewBox="0 0 16 16"><path d="M2 2.5h12v9H6l-3 2.5v-2.5H2z"/><path d="M4.5 5.5h7M4.5 8h5"/></symbol>
    <symbol id="i-report" viewBox="0 0 16 16"><rect x="3" y="1.5" width="10" height="13" rx="1"/><circle cx="6.5" cy="7" r="1.8"/><path d="M9.5 6h2M9.5 8h2M5 11h6"/></symbol>
    <symbol id="i-files" viewBox="0 0 16 16"><path d="M4 2.5h8v12H4z"/><path d="M2.5 4v11.5h8M6 5.5h4M6 8h4M6 10.5h4"/></symbol>
    <symbol id="i-tools" viewBox="0 0 16 16"><path d="M2.5 13.5l6-6M5 2.5l-2 2 3 3 2-2zM13.5 13.5l-5-5M10.5 2.5a2.5 2.5 0 0 0 3 3L11.8 7.2 8.8 4.2z"/></symbol>
    <symbol id="i-people" viewBox="0 0 18 18"><circle cx="9" cy="6" r="2.5"/><circle cx="4" cy="7" r="1.8"/><circle cx="14" cy="7" r="1.8"/><path d="M4.5 14c.8-3 2.5-4 4.5-4s3.7 1 4.5 4M1 13c.4-2 1.5-3 3-3M17 13c-.4-2-1.5-3-3-3"/></symbol>
    <symbol id="i-compass" viewBox="0 0 18 18"><circle cx="9" cy="9" r="8"/><circle cx="9" cy="9" r="3.5"/><path d="M9 1v3M9 14v3M1 9h3M14 9h3M6.5 6.5l5 5M11.5 6.5l-5 5"/></symbol>
  </defs>
</svg>

<div class="brand"><span class="brand-mark"></span>Keyhold</div>

<ul class="nav">
  <li class="current"><svg class="ic"><use href="#i-home"/></svg>Dashboard<span class="caret"></span></li>
  <li><svg class="ic"><use href="#i-user"/></svg>Customers</li>
  <li><svg class="ic"><use href="#i-home"/></svg>Properties</li>
  <li><svg class="ic"><use href="#i-user"/></svg>Tenants</li>
  <li><svg class="ic"><use href="#i-user"/></svg>Contacts</li>
  <li><svg class="ic"><use href="#i-gear"/></svg>Contractors</li>
  <li><svg class="ic"><use href="#i-user"/></svg>Employees</li>
  <li><svg class="ic"><use href="#i-doc"/></svg>Compliance Management</li>
  <li><svg class="ic"><use href="#i-gear"/></svg>Prevent. Maintenance<span class="more"></span></li>
  <li><svg class="ic"><use href="#i-gear"/></svg>Work Orders<span class="more"></span></li>
  <li><svg class="ic"><use href="#i-code"/></svg>Purchase Orders</li>
  <li><svg class="ic"><use href="#i-search"/></svg>Properly Inspections<span class="more"></span></li>
  <li><svg class="ic"><use href="#i-chart"/></svg>Energy Management</li>
  <li><svg class="ic"><use href="#i-warn"/></svg>Risk Management</li>
  <li><svg class="ic"><use href="#i-list"/></svg>Project Management</li>
  <li><svg class="ic"><use href="#i-money"/></svg>Financial - Budgeting</li>
  <li><svg class="ic"><use href="#i-chat"/></svg>Tenant Requests</li>
  <li><svg class="ic"><use href="#i-report"/></svg>Reports<span class="more"></span></li>
  <li><svg class="ic"><use href="#i-chart"/></svg>Visual Reports</li>
  <li><svg class="ic"><use href="#i-files"/></svg>Files</li>
  <li><svg class="ic"><use href="#i-files"/></svg>Pages<span class="more"></span></li>
  <li><svg class="ic"><use href="#i-gear"/></svg>Configurations<span class="more"></span></li>
  <li><svg class="ic"><use href="#i-tools"/></svg>Settings<span class="more"></span></li>
</ul>

<div class="topbar-home"><svg width="11" height="11" viewBox="0 0 16 16"><path d="M8 1.5 1 8h2v6.5h4v-4h2v4h4V8h2z" fill="#fff"/></svg></div>
<div class="topbar-title">Active Dashboard</div>

<div class="stat" style="left:497px;width:103px"><svg><use href="#i-home"/></svg><div>Properties<br>3</div></div>
<div class="stat" style="left:609px;width:102px"><svg><use href="#i-people"/></svg><div>Tenants<br>8</div></div>
<div class="stat" style="left:722px;width:152px"><svg><use href="#i-compass"/></svg><div>Total Properties area<br>422,000.00Sq.ft</div></div>
<div class="stat" style="left:884px;width:130px"><svg><use href="#i-compass"/></svg><div>Rented area<br>233,500.00sq.ft</div></div>
<div class="stat" style="left:1025px;width:130px"><svg><use href="#i-compass"/></svg><div>Vacancies area<br>188,500.00sq.ft</div></div>

<main class="card">
  <div class="tabs">
    <div class="tab selected"><i></i>LAST 7 DAYS</div>
    <div class="tab"><i></i>LAST MONTHS</div>
    <div class="tab"><i></i>LAST 3 MONTHS</div>
    <div class="tab"><i></i>NEXT 7 DAYS</div>
    <div class="tab"><i></i>NEXT MONTHS</div>
    <div class="tab"><i></i>NEXT 3 MONTHS</div>
  </div>
  <h1 class="range">12/27/2020 - 01/03/2021</h1>
  <div class="y-title">NUMBER</div>
  <svg class="chart" width="953" height="520" viewBox="0 0 953 520" font-family="Nunito Sans, sans-serif" font-size="9" fill="#4d5566">
    <g font-weight="600">
      <text x="52" y="155">1.25</text>
      <text x="52" y="213">1</text>
      <text x="52" y="272">0.75</text>
      <text x="52" y="331">0.5</text>
      <text x="52" y="389">0.25</text>
      <text x="52" y="448">0</text>
    </g>
    <line x1="81" y1="448.5" x2="916" y2="448.5" stroke="#dcdfe4" stroke-width="1"/>
    <rect x="417" y="139.5" width="15" height="309" rx="7.5" fill="var(--track)"/>
    <path d="M417 448.5V201a7.5 7.5 0 0 1 15 0v247.5z" fill="var(--blue)"/>
    <g text-anchor="middle" font-weight="600">
      <text x="112" y="479">12/27/2020</text>
      <text x="223" y="479">12/28/2020</text>
      <text x="335" y="479">12/29/2020</text>
      <text x="446" y="479">12/30/2020</text>
      <text x="557" y="479">12/31/2020</text>
      <text x="669" y="479">01/01/2021</text>
      <text x="780" y="479">01/02/2021</text>
      <text x="891" y="479">01/03/2021</text>
    </g>
  </svg>
  <div class="legend">
    <div class="legend-item" style="left:0"><span class="dot" style="background:var(--legend-blue)"></span>Sheduled<br>Maintenance</div>
    <div class="legend-item" style="left:128px"><span class="dot" style="background:var(--legend-green)"></span>Completed<br>Sheduled<br>Maintenance</div>
    <div class="legend-item" style="left:254px"><span class="dot" style="background:var(--legend-orange)"></span>Future Sheduled<br>Maintenance</div>
    <div class="legend-item" style="left:379px"><span class="dot" style="background:var(--legend-dark)"></span>Sheduled Work<br>Orders</div>
    <div class="legend-item" style="left:506px"><span class="dot" style="background:var(--legend-violet)"></span>Completed<br>Work Orders</div>
    <div class="legend-item" style="left:633px"><span class="dot" style="background:var(--legend-pink)"></span>Property<br>Inspections in<br>Progress</div>
    <div class="legend-item" style="left:760px"><span class="dot" style="background:var(--legend-yellow)"></span>Completed<br>Property<br>Inspections</div>
  </div>
</main>
</body>
</html>
```